TALMORK

The business want a professional looking business card. We have a scetch we will add but want the extra upgrade, and would like more suggestions for variations of our business cards.

```html
<!DOCTYPE html>
<html lang="en">
<head>
<meta charset="utf-8">
<title>Talmork Business Card</title>
<link rel="stylesheet" href="https://fonts.googleapis.com/css2?family=Cinzel:wght@600;700&family=Montserrat:wght@400;500;600&display=swap">
<style>
  :root {
    --page: #f0f0f0;
    --navy: #121826;
    --bronze: #5c4522;
    --gold: #c9a35a;
    --gold-light: #f1d78f;
    --gold-deep: #a47d3a;
    --ink: #1a1a1a;
  }
  * { margin: 0; padding: 0; box-sizing: border-box; }
  html, body { width: 935px; height: 1200px; overflow: hidden; background: var(--page); }
  .canvas { position: relative; width: 935px; height: 1200px; }

  .card {
    position: absolute; left: 88px; width: 760px; height: 456px;
    background: var(--navy); overflow: hidden;
    box-shadow: 8px 10px 14px rgba(0,0,0,0.28);
  }
  .card-front { top: 104px; }
  .card-back { top: 640px; }

  /* front */
  .front-brand {
    position: absolute; left: 0; right: 0; top: 128px; text-align: center;
    font-family: "Cinzel", serif; font-weight: 700; font-size: 92px;
    line-height: 1; color: var(--gold);
  }
  .front-tagline {
    position: absolute; left: 0; right: 0; top: 228px; text-align: center;
    font-family: "Montserrat", sans-serif; font-weight: 600; font-size: 20px;
    letter-spacing: 8px; color: var(--gold);
  }
  .front-band {
    position: absolute; left: 0; right: 0; top: 366px; bottom: 0; background: var(--bronze);
  }
  .front-rule {
    position: absolute; left: 0; right: 0; top: 360px; height: 5px;
    background: linear-gradient(90deg, var(--gold-deep), var(--gold-light), var(--gold-deep));
  }
  .web-pill {
    position: absolute; left: 214px; top: 334px; width: 332px; height: 58px;
    border-radius: 29px; background: var(--navy); padding: 4px;
  }
  .web-pill-inner {
    width: 100%; height: 100%; border-radius: 25px;
    border: 2px solid var(--gold);
    background: linear-gradient(180deg, var(--gold-light), var(--gold) 60%, var(--gold-deep));
    display: flex; align-items: center; justify-content: center;
    font-family: "Montserrat", sans-serif; font-weight: 500; font-size: 24px; color: var(--ink);
  }

  /* back */
  .side-band { position: absolute; left: 0; top: 0; bottom: 0; width: 88px; background: var(--bronze); }
  .side-rule {
    position: absolute; left: 87px; top: 0; bottom: 0; width: 7px;
    background: linear-gradient(90deg, var(--gold-deep), var(--gold-light), var(--gold-deep));
  }
  .icon-pill {
    position: absolute; left: 62px; width: 57px; border-radius: 29px;
    background: var(--navy); padding: 4px;
  }
  .icon-pill-inner {
    width: 100%; height: 100%; border-radius: 25px; border: 2px solid var(--gold);
    background: linear-gradient(90deg, var(--gold-deep), var(--gold-light) 50%, var(--gold-deep));
    display: flex; flex-direction: column; align-items: center; justify-content: space-around;
  }
  .icon-pill-person { top: 60px; height: 78px; }
  .icon-pill-contact { top: 226px; height: 176px; }
  .icon { width: 26px; height: 26px; fill: var(--ink); }

  .holder { position: absolute; left: 134px; top: 78px; }
  .holder-name {
    font-family: "Cinzel", serif; font-weight: 700; font-size: 35px; line-height: 1;
    color: var(--gold);
  }
  .holder-role {
    margin-top: 10px; font-family: "Montserrat", sans-serif; font-weight: 600;
    font-size: 22px; color: var(--gold); line-height: 1;
  }
  .holder-fullname {
    margin-top: 10px; font-family: "Montserrat", sans-serif; font-weight: 400;
    font-size: 16px; color: var(--gold); line-height: 1;
  }
  .contact-list { position: absolute; left: 134px; top: 253px; list-style: none; }
  .contact-list li {
    font-family: "Montserrat", sans-serif; font-weight: 400; font-size: 23px;
    color: var(--gold); line-height: 1; height: 46px;
  }

  .back-brand { position: absolute; left: 501px; width: 220px; top: 198px; text-align: center; }
  .brand-dot {
    width: 64px; height: 64px; border-radius: 50%; margin: 0 auto 14px;
    background: var(--gold);
  }
  .back-brand-name {
    font-family: "Cinzel", serif; font-weight: 700; font-size: 40px; line-height: 1; color: var(--gold);
  }
  .back-brand-tagline {
    margin-top: 4px; font-family: "Montserrat", sans-serif; font-weight: 600;
    font-size: 10px; letter-spacing: 4px; color: var(--gold);
  }
</style>
</head>
<body>
<main class="canvas">

  <section class="card card-front">
    <div class="front-brand">TALMORK</div>
    <div class="front-tagline">SINCE 2026</div>
    <div class="front-band"></div>
    <div class="front-rule"></div>
    <div class="web-pill"><div class="web-pill-inner">www.talmork.co</div></div>
  </section>

  <section class="card card-back">
    <div class="side-band"></div>
    <div class="side-rule"></div>

    <div class="icon-pill icon-pill-person">
      <div class="icon-pill-inner">
        <svg class="icon" viewBox="0 0 24 24" aria-hidden="true">
          <circle cx="12" cy="8" r="4.5"/>
          <path d="M3 21c0-4.5 4-7.5 9-7.5s9 3 9 7.5z"/>
        </svg>
      </div>
    </div>

    <div class="icon-pill icon-pill-contact">
      <div class="icon-pill-inner">
        <svg class="icon" viewBox="0 0 24 24" aria-hidden="true">
          <path d="M2 8c0-2 3-4 10-4s10 2 10 4v2h-5V8.5c-1.5-.6-3-.8-5-.8s-3.5.2-5 .8V10H2z"/>
          <path d="M6 11h12l2 9H4z"/>
        </svg>
        <svg class="icon" viewBox="0 0 24 24" aria-hidden="true">
          <path d="M2 6h20v12H2z M3.5 7.5 12 13.5l8.5-6" fill="none" stroke="#1a1a1a" stroke-width="0"/>
          <path d="M2 6h20l-10 7z"/>
          <path d="M2 8l10 7 10-7v10H2z"/>
        </svg>
        <svg class="icon" viewBox="0 0 24 24" aria-hidden="true">
          <g fill="none" stroke="#1a1a1a" stroke-width="1.8">
            <circle cx="12" cy="12" r="9"/>
            <ellipse cx="12" cy="12" rx="4" ry="9"/>
            <path d="M3 12h18M4.5 7.5h15M4.5 16.5h15"/>
          </g>
        </svg>
      </div>
    </div>

    <div class="holder">
      <div class="holder-name">TALMORK BREVIK</div>
      <div class="holder-role">CEO &amp; FOUNDER</div>
      <div class="holder-fullname">Oskar Lund Brevik</div>
    </div>

    <ul class="contact-list">
      <li>004791234567</li>
      <li>talmork.co@mailbox.com</li>
      <li>www.talmork.co</li>
    </ul>

    <div class="back-brand">
      <div class="brand-dot"></div>
      <div class="back-brand-name">TALMORK</div>
      <div class="back-brand-tagline">SINCE 2026</div>
    </div>
  </section>

</main>
</body>
</html>
```